Business Card Design for company

We want new business cards. We'd like something different-- yet still highly professional. Our tagline is Providing leadership, delivering success. Stock photos are ok, as long as they are relevant and look upscale.

Target Market(s)

Architecture/Business Management Consulting/Engineering Consulting

Contact Information for Business Card

dark gray background with pops of blue might be good, but you tell me. You're the designers. Rounded corners might be nice, but again, you tell me.

Font styles to use
Serif
Sans Serif

Colors
3276b5
5c5c5c
9d9d9d
fbfbfb

Requirements
Nice to have
• Something different, but still very professional.

```html
<!DOCTYPE html>
<html lang="en">
<head>
<meta charset="utf-8">
<title>Norvale Partners – Business Card</title>
<link href="https://fonts.googleapis.com/css2?family=Lato:wght@400;700;900&display=swap" rel="stylesheet">
<style>
  :root {
    --brand-blue: #28619a;
    --card-dark: #4a4e54;
    --ink-gray: #4b4f55;
    --rule-gray: #5c5c5c;
    --paper: #ffffff;
    --stage: #e6e6e4;
    --tagline: #f4f4f4;
  }
  * { box-sizing: border-box; margin: 0; padding: 0; }
  html, body {
    width: 1200px; height: 1108px; overflow: hidden;
    background: var(--stage);
    font-family: "Lato", Arial, sans-serif;
  }
  .card {
    position: absolute; left: 180px; width: 840px; height: 480px;
    box-shadow: 0 6px 18px rgba(0,0,0,0.18);
    overflow: hidden;
  }
  /* Back */
  .card-back { top: 56px; background: var(--card-dark); }
  .back-wordmark {
    position: absolute; left: 0; right: 0; top: 170px;
    text-align: center; color: var(--brand-blue);
    font-weight: 900; font-size: 96px; letter-spacing: 4px; line-height: 1;
  }
  .back-tagline {
    position: absolute; left: 0; right: 0; top: 300px;
    text-align: center; color: var(--tagline);
    font-size: 19px; letter-spacing: 0.5px;
  }
  .back-tagline .dot {
    display: inline-block; width: 8px; height: 8px; border-radius: 50%;
    background: var(--tagline); margin: 0 10px; vertical-align: middle;
  }
  /* Front */
  .card-front { top: 572px; background: var(--paper); }
  .holder { position: absolute; left: 44px; top: 62px; }
  .holder-name {
    color: var(--brand-blue); font-weight: 900; font-size: 28px;
    letter-spacing: 1px; text-transform: uppercase; line-height: 1;
  }
  .holder-title {
    color: var(--ink-gray); font-weight: 700; font-size: 18px;
    text-transform: uppercase; margin-top: 4px;
  }
  .divider {
    position: absolute; left: 44px; top: 128px; width: 560px; height: 2px;
    background: var(--rule-gray);
  }
  .contact-list {
    position: absolute; left: 44px; top: 146px; list-style: none;
    color: var(--ink-gray); font-size: 19px; line-height: 28px;
  }
  .contact-list li { display: flex; align-items: center; gap: 10px; }
  .contact-list svg { width: 16px; height: 16px; fill: var(--brand-blue); flex: none; }
  .contact-list .no-icon { padding-left: 26px; }
  .wordmark {
    position: absolute; right: 60px; top: 140px;
    display: flex; align-items: center; gap: 14px;
    color: var(--brand-blue); font-weight: 900; font-size: 62px; letter-spacing: 2px; line-height: 1;
  }
  .wordmark .mark-square { width: 22px; height: 22px; background: var(--brand-blue); }
  .address {
    position: absolute; right: 60px; top: 330px; text-align: right;
    color: var(--ink-gray); font-size: 22px; line-height: 30px;
  }
  .edge-band {
    position: absolute; left: 0; right: 0; bottom: 0; height: 14px;
    display: flex; gap: 3px;
  }
  .edge-band .seg-blue { background: var(--brand-blue); }
  .edge-band .seg-gray { background: var(--card-dark); }
</style>
</head>
<body>
  <section class="card card-back">
    <div class="back-wordmark">NORVALE</div>
    <p class="back-tagline">Providing leadership<span class="dot"></span>delivering success</p>
  </section>

  <section class="card card-front">
    <div class="holder">
      <div class="holder-name">Daniel Harper</div>
      <div class="holder-title">CEO/Founder</div>
    </div>
    <div class="divider"></div>
    <ul class="contact-list">
      <li><svg viewBox="0 0 16 16"><path d="M3.5 1l2.5 3-1.5 2c.8 2 2.5 3.7 4.5 4.5l2-1.5 3 2.5-1.5 3C6 14 2 10 .5 2.5z"/></svg>907 214 5580</li>
      <li><svg viewBox="0 0 16 16"><path d="M4 0h8a1 1 0 0 1 1 1v14a1 1 0 0 1-1 1H4a1 1 0 0 1-1-1V1a1 1 0 0 1 1-1zm1 2v10h6V2z"/></svg>907 388 1427</li>
      <li><svg viewBox="0 0 16 16"><path d="M4 1h8v4H4zM1 6h14v7h-3v2H4v-2H1zm4 4v4h6v-4z"/></svg>907 560 3391</li>
      <li><svg viewBox="0 0 16 16"><path d="M0 3h16v10H0zm1.5 1.2L8 9l6.5-4.8z"/></svg>daniel@norvalepartners.com</li>
    </ul>
    <div class="wordmark"><span class="mark-square"></span>NORVALE</div>
    <address class="address" style="font-style:normal">
      1420 Alder Crest Road<br>
      Juneau, Alaska 99801<br>
      www.norvalepartners.com
    </address>
    <div class="edge-band">
      <div class="seg-blue" style="flex:30"></div>
      <div class="seg-gray" style="flex:25"></div>
      <div class="seg-blue" style="flex:45"></div>
    </div>
  </section>
</body>
</html>
```